Business Card: RW Office Partners - Your organised problem solver

Business Name: RW Office Partners
Website: www.rwofficepartners.com.au
Email: marisol@rwofficepartners.com.au
Mobile: 61 482 907 236
Facebook: @rwofficepartners
Instrgram: @rwofficepartners

Brading Colours:
HEX
#986474
#ddccd3
#7a8498
#c9d8e4
#000000
#ffffff

Tag Line: Your organised problem solver

Link to DRAFT website:
https://deskhelpcollective.wixsite.com/rw-office-partners

About Page from the website:
My name is Marisol Wrenfield, and I would love to assist you to become more productive in your day to day and achieve your business and personal goals.
My mission is to give you time, time to work on the important tasks of your business or to be able to spend more time with your family. I will take on the tasks you don’t have time for, don’t know well or simply don’t like to do.
I have an extensive background in Administration, Tender Coordination, Document Control, WHS and Quality Management working primarily in the Construction, Mining and Corporate World.
I am passionate about being organised, having order and making things in your life (and mine) easier! I love to watch something unfold and grow into something amazing! I am known for being the go-to problem solver, the organiser of all things, producing high standards of work even under pressure. I’m also a confident communicator, and I understand that you’re busy running your business.

Target Market(s)

Small to Medium Business who require assistance in their business by a virtual assistant.

Industry/Entity Type

Virtual Assistant

Contact Information for Business Card

Mobile: 61 482 907 236

Font styles to use
Sans Serif

Colors
ffffff

Requirements
Must have
• Branding Colours as outlined.
Contact Details as outlined.
Logo as provided.
Proper contact details - mobile, facebook, instragm, website.
Simple, Elegant, very clean looking.
Should not have
• Note cute with pictures.
Not too girly as still want to market to construction companies.

```html
<!DOCTYPE html>
<html lang="en">
<head>
<meta charset="UTF-8">
<title>RW Office Partners – Business Card</title>
<link href="https://fonts.googleapis.com/css2?family=Roboto:wght@400;500&display=swap" rel="stylesheet">
<style>
  :root {
    --stage: #141415;
    --card: #1f1f20;
    --mauve: #986474;
    --slate: #7a8498;
    --ink-light: #f2f2f2;
    --tag: #e6e6e6;
    --back-name: #3b3b3d;
  }
  * { margin: 0; padding: 0; box-sizing: border-box; }
  html, body {
    width: 1200px; height: 900px; overflow: hidden;
    background: var(--stage);
    font-family: "Roboto", Arial, sans-serif;
  }
  .stage {
    width: 1200px; height: 900px;
    display: flex; flex-direction: column;
    align-items: center; justify-content: center; gap: 60px;
  }
  .card {
    position: relative;
    width: 560px; height: 342px;
    background: var(--card);
    border-radius: 3px;
  }
  /* Front */
  .brand-name {
    position: absolute; left: 34px; top: 112px; width: 220px;
    font-weight: 500; font-size: 28px; line-height: 1.15;
    color: var(--mauve); text-transform: uppercase; letter-spacing: 0.5px;
  }
  .divider {
    position: absolute; left: 268px; top: 116px;
    width: 1px; height: 112px; background: var(--mauve);
  }
  .contacts {
    position: absolute; left: 282px; top: 120px;
    list-style: none;
  }
  .contacts li {
    display: flex; align-items: center; gap: 8px;
    font-size: 14px; line-height: 26px; color: var(--ink-light);
  }
  .contacts svg { width: 14px; height: 14px; flex: none; }
  .social-mark {
    width: 12px; height: 12px; background: var(--slate); flex: none; margin: 0 1px;
  }
  .tagline {
    position: absolute; left: 34px; top: 262px;
    font-size: 15px; color: var(--tag);
  }
  /* Back */
  .card--back { display: flex; align-items: center; justify-content: center; }
  .back-name {
    font-weight: 500; font-size: 40px; color: var(--back-name);
    text-transform: uppercase; letter-spacing: 1px;
  }
</style>
</head>
<body>
<main class="stage">
  <section class="card card--front">
    <div class="brand-name">RW Office Partners</div>
    <div class="divider"></div>
    <ul class="contacts">
      <li>
        <svg viewBox="0 0 24 24" aria-hidden="true"><path fill="#986474" d="M6.6 10.8a15 15 0 0 0 6.6 6.6l2.2-2.2c.3-.3.7-.4 1-.2 1.1.4 2.3.6 3.6.6.6 0 1 .4 1 1V20c0 .6-.4 1-1 1A17 17 0 0 1 3 4c0-.6.4-1 1-1h3.5c.6 0 1 .4 1 1 0 1.3.2 2.5.6 3.6.1.3 0 .7-.2 1z"/></svg>
        61 482 907 236
      </li>
      <li>
        <svg viewBox="0 0 24 24" aria-hidden="true"><path fill="#986474" d="M3 5h18c.6 0 1 .4 1 1v12c0 .6-.4 1-1 1H3c-.6 0-1-.4-1-1V6c0-.6.4-1 1-1zm9 7.5L20.5 7h-17z"/></svg>
        marisol@rwofficepartners.com.au
      </li>
      <li>
        <svg viewBox="0 0 24 24" aria-hidden="true"><circle cx="12" cy="12" r="9" fill="none" stroke="#986474" stroke-width="2.4"/><path d="M3 12h18M12 3c3 3 3 15 0 18M12 3c-3 3-3 15 0 18" fill="none" stroke="#986474" stroke-width="1.8"/></svg>
        www.rwofficepartners.com.au
      </li>
      <li>
        <span class="social-mark" aria-hidden="true"></span>
        @rwofficepartners
      </li>
    </ul>
    <p class="tagline">Your organised problem solver</p>
  </section>

  <section class="card card--back">
    <div class="back-name">RW Office Partners</div>
  </section>
</main>
</body>
</html>
```